Companybrochure for Consulting & Financing Firm

I need to have a Company Brochure asap for our company. We have a website that describes what we do, but we need also a brochure, that can be sent by PDF of eventually be printed as well.

The brochure should be short but nice and appealing to the customers.

We provide professional management consulting and help our customers to get finance for very diferent projects. Our business has a lot to do with personal relations, but also we are very professional in the way we work and how develop the solutions for our clients. Our clients are mainly government-owned firm, but also private trading companies and wealthy private investors.

Our customers are mainly in Latin America, but the company is headquater is in Switzerland. We are opening offices in Panama and Caracas, this should be easaly be adabtable later.

Please have a look at our website www.vorelpartners.ch. In the brochure, we would segment our services in 1.) Project Developments 2.) Management Conulting 3.) Investment Management and 4.) Finance Solutions.

Also do have a look at www.vorelpartners.ch
(Click E for the English version)
Updates

I managed to put the Mock-Up to the Website.
It is actually not really a mock-up, it is a version I have designed myself.
Well as I am not a designer, I hope you can make it much better.
The content however is what I would put in any other design as well.

Target Market(s)

Top Management, Investors, Entrepreneurs, Government Officials

Industry/Entity Type

Management Consulting

Requirements
Must have
• Design should reflect this image elements:

We are entrepreneurs.
We are comitted to get things done.
We work closely with the client side by side.
We are a professional partner.
We are not afraid of delivering unconventional solutions.
We look at the problem from various angles.
We analyse, develop solutions and implent results.
Should not have
• Typical US-American style elements. We do not want to give the impression of being a US company.

We do not want to appear to be neo-liberal. We are a politically neutral professional consulting firm.

```html
<!DOCTYPE html>
<html lang="en">
<head>
<meta charset="utf-8">
<title>Vorel Partners AG – Finance Solutions</title>
<link rel="stylesheet" href="https://fonts.googleapis.com/css2?family=Arimo:wght@400;700&family=Open+Sans:wght@400;600;700&display=swap">
<style>
  :root {
    --canvas: #c6c6c6;
    --navy: #3a477d;
    --band: #3d4a7c;
    --title-bg: #e9e9ea;
    --panel-grey: #d3d3d4;
    --body-text: #5a5a5a;
    --white: #ffffff;
    --blue-deep: #2f4d8f;
    --blue-light: #1a9ae0;
  }
  * { margin: 0; padding: 0; box-sizing: border-box; }
  html, body { width: 1200px; height: 434px; overflow: hidden; background: var(--canvas); }
  body { position: relative; font-family: "Open Sans", Arial, sans-serif; }

  .page { position: absolute; top: 12px; width: 579px; height: 409px; background: var(--panel-grey); overflow: hidden; }
  .page--left { left: 17px; }
  .page--right { left: 605px; width: 578px; }

  .hero-photo {
    position: absolute; left: 0; top: 0; width: 100%; height: 210px;
    background: linear-gradient(100deg, #8e949c 0%, #c9cdd2 25%, #3c3f4a 40%, #d8d9dc 55%, #2e3038 70%, #c4b49a 90%, #9a8a72 100%);
  }
  .hero-band { position: absolute; left: 0; top: 210px; width: 100%; height: 14px; background: var(--band); }
  .title-strip { position: absolute; left: 0; top: 224px; width: 100%; height: 40px; background: var(--title-bg); }
  .section-title {
    position: absolute; left: 51px; top: 231px;
    font-family: "Arimo", Arial, sans-serif; font-weight: 700; font-size: 20px; color: var(--navy);
  }
  .intro { position: absolute; left: 51px; top: 274px; width: 500px; font-size: 8.6px; line-height: 12.5px; color: var(--body-text); }
  .intro p + p { margin-top: 12.5px; }

  .values-panel {
    position: absolute; left: 0; top: 0; width: 100%; height: 281px;
    background: radial-gradient(ellipse 260px 200px at 285px 135px, var(--blue-light) 0%, #1f74bf 45%, var(--blue-deep) 100%);
  }
  .tagline {
    position: absolute; left: 51px; top: 105px;
    font-family: "Arimo", Arial, sans-serif; font-weight: 700; font-size: 19px; color: var(--white);
  }
  .values { position: absolute; left: 51px; top: 151px; list-style: none; font-size: 10.4px; font-weight: 700; line-height: 15.4px; color: var(--white); }

  .registration { position: absolute; left: 51px; top: 301px; font-size: 10.4px; font-weight: 700; color: var(--navy); }
  .contact { position: absolute; left: 51px; top: 335px; font-size: 9.6px; line-height: 12px; color: var(--navy); font-style: normal; }
  .contact strong { font-weight: 700; }
</style>
</head>
<body>
  <section class="page page--left">
    <div class="hero-photo" role="img" aria-label="Photo of business people talking and laughing in a bright office"></div>
    <div class="hero-band"></div>
    <div class="title-strip"></div>
    <h1 class="section-title">&gt;&gt; Finance Solutions</h1>
    <div class="intro">
      <p>Financing growth opportunities sometimes calls for an entrepreneurial perspective, which is often not<br>found in the traditional banking world.</p>
      <p>That is why we have committed ourselves to developing financing solutions for unconventional requirements.<br>To do so, we often work with partners with complementary subject matter expertise and geographical coverage.</p>
      <p>This gives us the flexibility to create innovative solutions – solutions that meet our clients' special needs.</p>
    </div>
  </section>

  <section class="page page--right">
    <div class="values-panel">
      <h2 class="tagline">&gt; Analyze &gt;&gt; Develop &gt;&gt;&gt; Deliver</h2>
      <ul class="values">
        <li>We are entrepreneurs.</li>
        <li>&gt; We are committed to get things done.</li>
        <li>&gt; We work closely with the client side by side.</li>
        <li>&gt; We apply structured methods of reasoning.</li>
        <li>&gt; We look at the problem from various angles.</li>
        <li>&gt; We are not afraid of delivering unconventional solutions.</li>
        <li>&gt; We analyze situations, develop solutions and implement results.</li>
      </ul>
    </div>
    <p class="registration">Vorel Partners AG is registered as a Swiss stock corporation since 1995.</p>
    <address class="contact">
      <strong>Vorel Partners AG</strong><br>
      Lindenweg 14, CH-8004 Zürich<br>
      Tel. +41 44 000 12 30 | Fax. +41 44 000 12 39<br>
      www.vorelpartners.ch | info@vorelpartners.ch
    </address>
  </section>
</body>
</html>
```